Harbor Crestline (Business Card Design)

Need business cards designed. Something modern, chic, and sleek. Mabye the back of the card should be the navy blue that is in the logo and then just the logo on the back.

Target Market(s)

Those in the hotel, office, and renovation industry

Contact Information for Business Card

1. Logo 2. Dorian Fenwick 3. CEO/Founder 4. Phone: (833) HarbCre / (833) 427-2731 5. Email: dorian@theharborcrestline.com 6. Website: www.theharborcrestline.com

Font styles to use
Other font styles liked:
• Look at the logo font and base the font for everything else off of that.

Colors
0054AA
0677BA
7BADD7
CADEEF
E8F1F8

Requirements
Must have
• Colors that are associated in the logo
Nice to have
• Sleek modern clean and chic design.

```html
<!DOCTYPE html>
<html lang="en">
<head>
<meta charset="utf-8">
<title>Harbor Crestline – Business Card</title>
<link href="https://fonts.googleapis.com/css2?family=Open+Sans:wght@400;600;700&display=swap" rel="stylesheet">
<style>
  :root {
    --backdrop: #2b2b2e;
    --navy: #0c1740;
    --navy-raised: #1c2a63;
    --gold: #c9a04a;
    --white: #ffffff;
    --rule: rgba(255,255,255,0.45);
  }
  * { margin: 0; padding: 0; box-sizing: border-box; }
  html, body {
    width: 1200px; height: 780px; overflow: hidden;
    background: var(--backdrop);
    font-family: "Open Sans", Arial, sans-serif;
  }
  .sheet {
    position: relative; width: 1200px; height: 780px;
    display: flex; align-items: center; justify-content: center; gap: 50px;
  }
  .card {
    position: relative; width: 525px; height: 300px;
    background: var(--navy); overflow: hidden;
    box-shadow: 0 10px 30px rgba(0,0,0,0.45);
  }

  /* Front */
  .wordmark {
    position: absolute; display: flex; align-items: center; gap: 12px;
    color: var(--white); font-weight: 600; letter-spacing: 0.14em;
  }
  .card-front .wordmark { top: 52px; left: 250px; font-size: 17px; }
  .wordmark-square { width: 30px; height: 30px; background: currentColor; flex: none; }

  .person { position: absolute; left: 40px; top: 118px; text-align: right; width: 170px; }
  .person-name { font-size: 24px; font-weight: 700; line-height: 1.1; color: var(--white); }
  .person-name .first { color: var(--gold); }
  .person-title { margin-top: 6px; font-size: 13px; color: var(--white); }

  .divider {
    position: absolute; left: 228px; top: 118px; width: 1px; height: 100px;
    background: var(--rule);
  }

  .contacts { position: absolute; left: 246px; top: 130px; list-style: none; }
  .contacts li {
    display: flex; align-items: center; gap: 8px;
    font-size: 12.5px; color: var(--white); line-height: 1; margin-bottom: 12px;
  }
  .contacts svg { width: 13px; height: 13px; flex: none; }

  .address-band {
    position: absolute; left: 0; right: 0; bottom: 0; height: 34px;
    background: var(--gold); color: var(--white);
    display: flex; align-items: center; padding-left: 40px;
    font-size: 13.5px; font-weight: 600;
  }

  /* Back */
  .card-back { display: flex; align-items: center; justify-content: center; }
  .card-back .wordmark {
    position: static; color: var(--navy-raised); font-size: 26px; gap: 16px;
  }
  .card-back .wordmark-square { width: 42px; height: 42px; }
</style>
</head>
<body>
<main class="sheet">

  <section class="card card-front" aria-label="Business card front">
    <div class="wordmark"><span class="wordmark-square"></span>HARBOR CRESTLINE</div>

    <div class="person">
      <p class="person-name"><span class="first">Dorian</span> Fenwick</p>
      <p class="person-title">CEO/Founder</p>
    </div>

    <div class="divider"></div>

    <ul class="contacts">
      <li>
        <svg viewBox="0 0 16 16" aria-hidden="true"><path fill="#c9a04a" d="M3.6 1.5l2.3 2.6-1.3 1.6c.9 2 2.6 3.7 4.7 4.7l1.6-1.3 2.6 2.3-1.4 2.1C7.1 13.2 2.8 8.9 1.5 3z"/></svg>
        (833) HarbCre / (833) 427-2731
      </li>
      <li>
        <svg viewBox="0 0 16 16" aria-hidden="true"><circle cx="8" cy="8" r="6.5" fill="none" stroke="#c9a04a" stroke-width="1.6"/><path d="M1.5 8h13M8 1.5c-3 3.5-3 9.5 0 13M8 1.5c3 3.5 3 9.5 0 13" fill="none" stroke="#c9a04a" stroke-width="1.2"/></svg>
        www.theharborcrestline.com
      </li>
      <li>
        <svg viewBox="0 0 16 16" aria-hidden="true"><rect x="1.5" y="3.5" width="13" height="9" fill="none" stroke="#c9a04a" stroke-width="1.6"/><path d="M1.5 3.5L8 9l6.5-5.5" fill="none" stroke="#c9a04a" stroke-width="1.4"/></svg>
        dorian@theharborcrestline.com
      </li>
    </ul>

    <div class="address-band">4120 Larkspur Ave Suite 210, Fairhaven, MD 20917</div>
  </section>

  <section class="card card-back" aria-label="Business card back">
    <div class="wordmark"><span class="wordmark-square"></span>HARBOR CRESTLINE</div>
  </section>

</main>
</body>
</html>
```